Luxury WordPress Website for CORALBASINS

I need a professional WordPress website for Coral Basins. The site should be modern, visually appealing, and user-friendly, reflecting the brand’s luxury and premium identity. It must include a homepage, product/service pages, contact form, and be responsive on both desktop and mobile devices. The design should allow for easy updates and integration of future content, while maintaining a polished and professional look.

Target Market(s)

swimmingpool & spa

Industry/Entity Type

Swimmingpool

Coding

Coded - Design and coding required

Font styles to use
Other font styles liked:
• HaboroSoft

Requirements
Must have
• Exclusive appearance
Nice to have
• • A logo that subtly incorporates water or pool elements. • A color palette that reflects luxury, elegance, and relaxation. • Clean and modern typography that is easy to read across all media. • Iconography or design elements that convey premium quality. • A versatile design that can be adapted for social media, merchandise, and promotional materials. • Optional: A tagline that emphasizes luxury and high-end pool experiences.

```html
<!DOCTYPE html>
<html lang="en">
<head>
<meta charset="utf-8">
<title>Coral Basins — Where Design Meets Durability</title>
<link href="https://fonts.googleapis.com/css2?family=Montserrat:wght@500;600;700;800&family=Inter:ital,wght@0,400;0,500;0,600;1,400&display=swap" rel="stylesheet">
<style>
:root{
  --navy:#0c3358;
  --navy-deep:#0a2b4b;
  --blue:#2a74c9;
  --blue-bright:#1f6dc4;
  --blue-soft:#3d87d9;
  --water:#4fb6e0;
  --ink:#1b1f27;
  --text:#3c4350;
  --white:#ffffff;
  --line:#e3e8ef;
}
*{box-sizing:border-box;margin:0;padding:0}
html,body{width:1200px;height:4549px;overflow:hidden}
body{position:relative;background:var(--white);font-family:"Inter",sans-serif;color:var(--text)}
.abs{position:absolute}
h1,h2,h3,h4,.brand,.btn{font-family:"Montserrat",sans-serif}
.section-title{position:absolute;left:0;width:1200px;text-align:center;font-weight:800;font-size:42px;color:var(--navy);letter-spacing:.5px}
.section-lead{position:absolute;left:220px;width:760px;text-align:center;font-size:15.5px;line-height:26px;color:var(--text)}
.btn{position:absolute;display:flex;align-items:center;justify-content:center;border-radius:26px;background:var(--blue-bright);color:var(--white);font-weight:700;font-size:15px;box-shadow:0 3px 6px rgba(0,0,0,.25)}
.btn-dark{background:var(--navy)}

/* header */
.topbar{left:498px;top:0;width:592px;height:42px;background:var(--blue-bright);border-radius:0 0 0 26px;display:flex;align-items:center;color:var(--white);font-size:13px;font-weight:500}
.topbar .tab{display:flex;align-items:center;gap:8px;padding-left:38px}
.topbar .tab.mail{margin-left:auto;height:42px;padding:0 30px 0 40px;background:var(--navy);border-radius:0 0 0 26px}
.brand-mark{left:112px;top:22px;display:flex;align-items:center;gap:10px}
.brand-mark .dot{width:30px;height:30px;border-radius:50%;background:var(--blue-bright)}
.brand-mark .name{font-weight:800;font-size:21px;color:var(--navy);letter-spacing:.5px}
.nav{left:486px;top:69px;display:flex;gap:38px;font-size:15px;font-weight:500;color:var(--ink)}
.social{display:flex;gap:8px}
.social span{width:28px;height:28px;border-radius:50%;border:1.8px solid var(--ink)}
.social.head{left:915px;top:64px}

/* hero */
.hero-title{left:122px;top:262px;color:var(--white);font-weight:800;font-size:43px;line-height:60px;letter-spacing:.5px}
.hero-copy{left:122px;top:394px;width:580px;color:var(--white);font-size:16px;line-height:26px;font-weight:500}
.hero-dots{left:44px;top:282px;display:flex;flex-direction:column;gap:13px;align-items:center}
.hero-dots span{width:17px;height:17px;border-radius:50%;background:var(--blue-soft)}
.hero-dots span.on{width:28px;height:28px;border:2.5px solid #9cc6f0;background:var(--blue-soft);box-shadow:inset 0 0 0 4px var(--navy)}
.feature{text-align:center;width:320px}
.feature .ic{width:88px;height:88px;margin:0 auto;border-radius:50%;background:var(--blue-bright);border:4px solid #e6eef8;display:flex;align-items:center;justify-content:center}
.feature p{margin-top:14px;font-family:"Montserrat",sans-serif;font-weight:700;font-size:16px;color:var(--ink)}

/* about */
.about-title{left:112px;top:888px;font-weight:800;font-size:40px;color:var(--navy)}
.about-lead{left:112px;top:950px;width:460px;font-size:14.5px;line-height:25px}
.about-body{left:668px;top:890px;width:420px;font-size:14.5px;line-height:25.5px}
.about-body p+p{margin-top:22px}
.photo{border-radius:12px}

/* process */
.step{width:314px;height:314px;border-radius:50%;overflow:hidden;background:var(--blue-bright);text-align:center;color:var(--white)}
.step svg.wave{position:absolute;left:0;top:0}
.step .ic{position:absolute;left:101px;top:53px;width:112px;height:112px;border-radius:50%;background:#f5f4f1;display:flex;align-items:center;justify-content:center}
.step h3{position:absolute;top:176px;width:100%;font-size:18.5px;font-weight:700}
.step p{position:absolute;top:214px;left:52px;width:210px;font-size:14.5px;line-height:21px}

/* collections */
.band{left:0;top:1990px;width:1200px;height:434px;background:linear-gradient(180deg,#2a76cc,#3b89da 60%,#2f7ad0)}
.collection-img{width:312px;height:200px;border-radius:10px 10px 0 0}
.collection-card{width:274px;height:180px;background:var(--white);border-radius:6px;box-shadow:0 4px 14px rgba(0,0,0,.12);text-align:center}
.collection-card h3{margin-top:18px;font-size:17px;font-weight:700;color:var(--ink)}
.collection-card p{margin:15px auto 0;width:232px;font-size:14.5px;line-height:26px}
.arrow{width:46px;height:46px;border-radius:50%;display:flex;align-items:center;justify-content:center}

/* testimonials */
.review{width:302px;height:290px;background:var(--white);box-shadow:0 2px 12px rgba(0,0,0,.12)}
.review .avatar{position:absolute;left:21px;top:22px;width:76px;height:76px;border-radius:50%;border:3px solid var(--blue-bright);background:linear-gradient(160deg,#b8c3cc,#6e7f8c)}
.review h4{position:absolute;left:108px;top:29px;font-size:17px;font-weight:700;color:var(--ink)}
.review .date{position:absolute;left:108px;top:56px;font-size:13px;color:#555}
.review p{position:absolute;left:21px;top:115px;width:262px;font-size:13px;line-height:24px;font-style:italic;color:#555}

/* footer */
.footer-col h4{font-size:18px;font-weight:700;color:var(--white)}
.contact-row{display:flex;align-items:flex-start;gap:14px;color:var(--white);font-size:15px;line-height:25px;margin-top:18px}
.contact-row .pin{flex:none;width:32px;height:32px;border-radius:50%;background:var(--blue-bright);display:flex;align-items:center;justify-content:center}
.quick a{display:block;color:var(--white);text-decoration:none;font-size:16.5px;margin-top:15px}
.footer-brand{left:444px;top:4210px;width:380px;display:flex;align-items:center;gap:14px}
.footer-brand .dot{width:56px;height:56px;border-radius:50%;background:var(--white);flex:none}
.footer-brand .name{font-weight:800;font-size:29px;color:var(--white);letter-spacing:.5px}
.social.foot span{width:36px;height:36px;border-color:var(--white)}
.copy{left:0;top:4494px;width:1200px;text-align:center;color:#d7e0ea;font-size:15px}
</style>
</head>
<body>

<!-- header -->
<div class="abs brand-mark">
  <span class="dot"></span>
  <div class="brand name">CORAL BASINS</div>
</div>
<div class="abs topbar">
  <div class="tab"><svg width="14" height="14" viewBox="0 0 24 24"><path fill="#fff" d="M6.6 10.8a15.1 15.1 0 0 0 6.6 6.6l2.2-2.2a1 1 0 0 1 1-.25 11.4 11.4 0 0 0 3.6.57 1 1 0 0 1 1 1V20a1 1 0 0 1-1 1A17 17 0 0 1 3 4a1 1 0 0 1 1-1h3.5a1 1 0 0 1 1 1c0 1.25.2 2.45.57 3.570a1 1 0 0 1-.25 1z"/></svg>CALL US TODAY! 555-014-2290</div>
  <div class="tab mail"><svg width="14" height="12" viewBox="0 0 24 18"><path fill="#fff" d="M0 0h24v18H0zM12 10 2 2v2l10 8 10-8V2z"/></svg>INFO@CORALBASINS.COM</div>
</div>
<nav class="abs nav"><span>HOME</span><span>PRODUCT</span><span>SERVICE</span><span>CONTACT</span></nav>
<div class="abs social head"><span></span><span></span><span></span><span></span><span></span></div>

<!-- hero -->
<svg class="abs" style="left:0;top:0" width="1200" height="760" role="img" aria-label="Evening view of a modern glass villa with lit terraces and an infinity pool">
  <defs>
    <linearGradient id="heroFill" x1="0" y1="0" x2="1" y2="0.6">
      <stop offset="0" stop-color="#0b3159"/>
      <stop offset=".55" stop-color="#14426d"/>
      <stop offset=".8" stop-color="#5a5448"/>
      <stop offset="1" stop-color="#2a4f72"/>
    </linearGradient>
  </defs>
  <path d="M0 113H1200V621Q600 825 0 621Z" fill="url(#heroFill)"/>
</svg>
<div class="abs hero-dots"><span class="on"></span><span></span><span></span><span></span></div>
<h1 class="abs hero-title">CORAL BASINS<br>WHERE DESIGN MEETS DURABILITY</h1>
<p class="abs hero-copy">Exclusive pools crafted for those who demand excellence in form, finish, and performance.</p>
<div class="btn" style="left:122px;top:465px;width:256px;height:48px;border:2px solid #9cc6f0">Explore Collections</div>

<div class="abs feature" style="left:78px;top:651px">
  <div class="ic"><svg width="40" height="46" viewBox="0 0 40 46" fill="none" stroke="#fff" stroke-width="2.5"><path d="M6 3h28M6 43h28M10 3c0 12 20 14 20 20S10 31 10 43M30 3c0 12-20 14-20 20s20 8 20 20"/></svg></div>
  <p>Lifetime Structural Warranty</p>
</div>
<div class="abs feature" style="left:424px;top:679px">
  <div class="ic"><svg width="44" height="44" viewBox="0 0 24 24" fill="none" stroke="#fff" stroke-width="1.6"><circle cx="12" cy="12" r="3.2"/><path d="M12 2v3M12 19v3M2 12h3M19 12h3M4.9 4.9l2.1 2.1M17 17l2.1 2.1M4.9 19.1 7 17M17 7l2.1-2.1"/></svg></div>
  <p>Custom Design Studio</p>
</div>
<div class="abs feature" style="left:773px;top:648px">
  <div class="ic"><svg width="44" height="40" viewBox="0 0 26 22" fill="none" stroke="#fff" stroke-width="1.6"><path d="M1 3h14v12H1zM15 7h5l4 4v4h-9"/><circle cx="6" cy="17" r="2.4"/><circle cx="19" cy="17" r="2.4"/></svg></div>
  <p>Nationwide Delivery &amp; Installation</p>
</div>

<!-- about -->
<h2 class="abs about-title">ABOUT US</h2>
<p class="abs about-lead">Lorem ipsum dolor sit amet, consectetur adipiscing elit, sed do eiusmod tempor incididunt ut labore et dolore magna aliqua. Ut enim ad minim veniam, quis nostrud</p>
<div class="abs photo" style="left:110px;top:1050px;width:498px;height:272px;background:linear-gradient(135deg,#a86b3e 0%,#2fa6d6 22%,#46c3e8 60%,#1c83bf 88%,#8b5a34 100%)" role="img" aria-label="Terraced pool with built-in steps and timber decking"></div>
<div class="abs about-body">
  <p>Lorem ipsum dolor sit amet, consectetur adipiscing elit, sed do eiusmod tempor incididunt ut labore et dolore magna aliqua. Ut enim ad minim veniam, quis nostrud exercitation ullamco laboris nisi ut aliquip ex ea commodo consequat. Duis aute irure dolor in reprehenderit in voluptate velit esse cillum dolore eu fugiat nulla pariatur.</p>
  <p>Lorem ipsum dolor sit amet, consectetur adipiscing elit, sed do eiusmod tempor incididunt ut labore et dolore magna aliqua. Ut enim ad minim veniam, quis nostrud exercitation ullamco laboris nisi ut aliquip ex ea commodo consequat. Duis aute irure dolor in reprehenderit in voluptate velit esse cillum dolore eu fugiat nulla pariatur.</p>
</div>
<div class="btn btn-dark" style="left:662px;top:1272px;width:146px;height:48px">Read More</div>

<!-- process -->
<h2 class="section-title" style="top:1408px">HOW WE BUILD EXCELLENCE</h2>
<p class="section-lead" style="top:1478px">Lorem ipsum dolor sit amet, consectetur adipiscing elit, sed do eiusmod tempor incididunt ut labore et dolore magna aliqua. Ut enim ad minim veniam, quis nostrud</p>

<div class="abs step" style="left:111px;top:1579px">
  <svg class="wave" width="314" height="314"><path d="M0 0H314V168Q270 140 226 158T140 160T60 150T0 170Z" fill="var(--navy)"/></svg>
  <div class="ic"><svg width="58" height="58" viewBox="0 0 32 32" fill="none" stroke="#222" stroke-width="1.5"><rect x="6" y="8" width="12" height="9"/><circle cx="23" cy="13" r="3"/><path d="M18 28v-6a5 5 0 0 1 10 0v6M3 20h19M10 20v8"/></svg></div>
  <h3>Design Consultation</h3>
  <p>We start with understanding your vision, space, and lifestyle.</p>
</div>
<div class="abs step" style="left:443px;top:1579px">
  <svg class="wave" width="314" height="314"><path d="M0 0H314V168Q270 140 226 158T140 160T60 150T0 170Z" fill="var(--navy)"/></svg>
  <div class="ic"><svg width="62" height="44" viewBox="0 0 40 28" fill="none" stroke="#222" stroke-width="1.5"><path d="M4 8h28l4 6H8zM8 14v8h28v-8M12 14v8M18 14v8M24 14v8M30 14v8M6 4h24"/></svg></div>
  <h3>Precision Fabrication</h3>
  <p>Every pool is engineered using the highest-grade materials</p>
</div>
<div class="abs step" style="left:774px;top:1579px">
  <svg class="wave" width="314" height="314"><path d="M0 0H314V168Q270 140 226 158T140 160T60 150T0 170Z" fill="var(--navy)"/></svg>
  <div class="ic"><svg width="54" height="58" viewBox="0 0 28 30" fill="none" stroke="#222" stroke-width="1.5"><path d="M8 28v-8l-4-6 2-1 4 4V4a1.5 1.5 0 0 1 3 0v9V2a1.5 1.5 0 0 1 3 0v11V4a1.5 1.5 0 0 1 3 0v10l3-3 2 1-4 8v8zM22 4l1 2 2 1-2 1-1 2-1-2-2-1 2-1z"/></svg></div>
  <h3>White-Glove Installation</h3>
  <p>Our installation team ensures flawless execution on-site</p>
</div>

<!-- collections -->
<div class="abs band"></div>
<h2 class="section-title" style="top:2058px;color:var(--white)">FEATURED COLLECTIONS</h2>
<p class="section-lead" style="top:2129px;color:var(--white)">Lorem ipsum dolor sit amet, consectetur adipiscing elit, sed do eiusmod tempor incididunt ut labore et dolore magna aliqua. Ut enim ad minim veniam, quis nostrud</p>

<div class="abs collection-img" style="left:110px;top:2230px;background:linear-gradient(180deg,#b9d6ea 0%,#7ea7c4 45%,#2f7fb6 70%,#1c6aa3 100%)" role="img" aria-label="Guest in an infinity edge pool overlooking the sea"></div>
<div class="abs collection-img" style="left:445px;top:2230px;background:linear-gradient(150deg,#eef4f8 0%,#2fa2e0 35%,#1b7fd0 65%,#9fd6f2 100%)" role="img" aria-label="Curved fiberglass pool shell with white surround"></div>
<div class="abs collection-img" style="left:779px;top:2230px;background:linear-gradient(180deg,#2e5a3b 0%,#4c7a52 35%,#2cb6e2 62%,#61cdef 100%)" role="img" aria-label="Architectural pool with steel ladder and tropical garden"></div>

<div class="abs collection-card" style="left:129px;top:2415px"><h3>Infinity Edge Series</h3><p>Experience seamless design with water that flows into the horizon. The perfect</p></div>
<div class="abs collection-card" style="left:464px;top:2415px"><h3>Signature Fiberglass</h3><p>Engineered for strength and simplicity, our fiberglass pools deliver elegance with low</p></div>
<div class="abs collection-card" style="left:798px;top:2415px"><h3>Architectural Custom</h3><p>From concept to completion, we tailor every detail — shape, materials, and finishes</p></div>
<div class="btn btn-dark" style="left:196px;top:2574px;width:144px;height:48px">View Model</div>
<div class="btn btn-dark" style="left:531px;top:2574px;width:144px;height:48px">View Model</div>
<div class="btn btn-dark" style="left:865px;top:2574px;width:144px;height:48px">View Model</div>

<div class="abs arrow" style="left:44px;top:2402px;background:#5f9be0"><svg width="12" height="20" viewBox="0 0 12 20"><path d="M10 2 2 10l8 8" fill="none" stroke="#fff" stroke-width="2"/></svg></div>
<div class="abs arrow" style="left:1114px;top:2402px;background:var(--blue-bright);border:2px solid #fff"><svg width="12" height="20" viewBox="0 0 12 20"><path d="m2 2 8 8-8 8" fill="none" stroke="#fff" stroke-width="2"/></svg></div>

<!-- past projects -->
<h2 class="section-title" style="top:2768px">PAST PROJECTS</h2>
<p class="section-lead" style="top:2838px">Lorem ipsum dolor sit amet, consectetur adipiscing elit, sed do eiusmod tempor incididunt ut labore et dolore magna aliqua. Ut enim ad minim veniam, quis nostrud</p>

<div class="abs" style="left:112px;top:2930px;width:313px;height:248px;background:linear-gradient(180deg,#7fb8e8 0%,#cfe6f5 35%,#2bc4d8 60%,#1796c4 100%)" role="img" aria-label="Beachfront infinity pool with umbrellas"></div>
<div class="abs" style="left:443px;top:2930px;width:313px;height:515px;background:linear-gradient(180deg,#9cc6ea 0%,#cfe2ef 25%,#3aaedb 50%,#23a7dc 100%)" role="img" aria-label="Infinity pool edge meeting the ocean horizon"></div>
<div class="abs" style="left:775px;top:2930px;width:313px;height:248px;background:linear-gradient(180deg,#5d8f6d 0%,#b39a78 35%,#2aa4dc 60%,#48b8e6 100%)" role="img" aria-label="Resort pool with chrome ladder and timber deck"></div>
<div class="abs" style="left:112px;top:3198px;width:313px;height:247px;background:linear-gradient(160deg,#b88a5a 0%,#d7b48b 25%,#48bfe4 50%,#7fd3ee 100%)" role="img" aria-label="Pool with curved entry steps beside wooden decking"></div>
<div class="abs" style="left:775px;top:3198px;width:313px;height:247px;background:linear-gradient(180deg,#5b4a3c 0%,#4e6f4a 35%,#1ea2d4 60%,#33b2e0 100%)" role="img" aria-label="Garden pool in front of a stone villa"></div>

<!-- testimonials -->
<h2 class="section-title" style="top:3570px">WHAT PEOPLE SAYS ABOUT US</h2>
<p class="abs" style="left:0;top:3633px;width:1200px;text-align:center;font-size:16px;color:var(--text)">Lorem ipsum dolor sit amet, consectetur adipiscing elit, sed do eiusmod</p>

<div class="abs review" style="left:110px;top:3695px"><div class="avatar" role="img" aria-label="Client portrait"></div><h4>MARA ELLSWORTH</h4><span class="date">01 Oct 2025</span><p>Sed ut perspiciatis unde omnis iste natus error sit voluptatem accusantium doloremque laudantium, totam rem aperiam, eaque ipsa quae ab illo inventore veritatis et quasi architecto beatae vitae dicta sunt explicabo.</p></div>
<div class="abs review" style="left:448px;top:3695px"><div class="avatar" role="img" aria-label="Client portrait"></div><h4>MARA ELLSWORTH</h4><span class="date">01 Oct 2025</span><p>Sed ut perspiciatis unde omnis iste natus error sit voluptatem accusantium doloremque laudantium, totam rem aperiam, eaque ipsa quae ab illo inventore veritatis et quasi architecto beatae vitae dicta sunt explicabo.</p></div>
<div class="abs review" style="left:786px;top:3695px"><div class="avatar" role="img" aria-label="Client portrait"></div><h4>MARA ELLSWORTH</h4><span class="date">01 Oct 2025</span><p>Sed ut perspiciatis unde omnis iste natus error sit voluptatem accusantium doloremque laudantium, totam rem aperiam, eaque ipsa quae ab illo inventore veritatis et quasi architecto beatae vitae dicta sunt explicabo.</p></div>

<div class="abs arrow" style="left:49px;top:3832px;background:var(--blue-bright)"><svg width="12" height="20" viewBox="0 0 12 20"><path d="M10 2 2 10l8 8" fill="none" stroke="#fff" stroke-width="2"/></svg></div>
<div class="abs arrow" style="left:1100px;top:3832px;background:var(--blue-bright)"><svg width="12" height="20" viewBox="0 0 12 20"><path d="m2 2 8 8-8 8" fill="none" stroke="#fff" stroke-width="2"/></svg></div>

<!-- footer -->
<svg class="abs" style="left:0;top:3960px" width="1200" height="589"><path d="M0 205Q600 5 1200 205V589H0Z" fill="var(--navy-deep)"/></svg>

<div class="abs footer-col" style="left:126px;top:4190px;width:320px">
  <h4>GET IN TOUCH</h4>
  <div class="contact-row"><span class="pin"><svg width="12" height="16" viewBox="0 0 12 16"><path d="M6 0a6 6 0 0 1 6 6c0 4-6 10-6 10S0 10 0 6a6 6 0 0 1 6-6zm0 3.5A2.5 2.5 0 1 0 6 8.5 2.5 2.5 0 0 0 6 3.5z" fill="#fff"/></svg></span><span>48 Harbor Lane, Ste 12<br>Marlow, Georgia, 30012</span></div>
  <div class="contact-row"><span class="pin"><svg width="14" height="14" viewBox="0 0 24 24"><path fill="#fff" d="M6.6 10.8a15.1 15.1 0 0 0 6.6 6.6l2.2-2.2a1 1 0 0 1 1-.25 11.4 11.4 0 0 0 3.6.57 1 1 0 0 1 1 1V20a1 1 0 0 1-1 1A17 17 0 0 1 3 4a1 1 0 0 1 1-1h3.5a1 1 0 0 1 1 1c0 1.25.2 2.45.57 3.57a1 1 0 0 1-.25 1z"/></svg></span><span>+1 555-014-2290</span></div>
  <div class="contact-row"><span class="pin"><svg width="14" height="11" viewBox="0 0 24 18"><path fill="#fff" d="M0 0h24v18H0zM12 10 2 2v2l10 8 10-8V2z"/></svg></span><span>info@coralbasins.com</span></div>
</div>

<div class="abs footer-brand">
  <span class="dot"></span>
  <div class="brand name">CORAL BASINS</div>
</div>
<div class="abs social foot" style="left:492px;top:4375px"><span></span><span></span><span></span><span></span><span></span></div>

<div class="abs footer-col quick" style="left:876px;top:4190px">
  <h4>QUICK LINKS</h4>
  <a>Home</a><a>Product</a><a>Service</a><a>Contact</a>
</div>

<p class="abs copy">© 2025 Coral Basins. All Rights Reserved.</p>

</body>
</html>
```